Design and Renovation Company Luxury Business Card

I want to create a luxury business card for a Design and Renovation Firm . We will use our current logo. The company name is 528BUILDA. We do not want anything standard. We need a very unique concept.
Please see uploaded inspiration. I really like the textured paper option. I would like the card to be thick with debossing, and/or embossing options. The logo has orange in it but I would like to see the card with and without the orange. I think the orange may make the company feel less high-end. The goal is to elevate the logo not match its vibe per se of the logo. We want something very unique, not standard at all!
I would like a space for :
Logo,
Name,
Position,
Email,
Office number,
Website Address,
Business Address,
Thank you!
Have fun!
Target Market(s)
Home owners Age 35 +
Industry/Entity Type
Design and Renovation
Contact Information for Business Card
Logo, Name, Position, Email, Office number, Website Address, Business Address,.
Colors
Designer to choose colors to be used in the design.
Requirements
Must have
- A luxury designer feel. Must be black or dark grey but open to other luxury ideas.
Nice to have
- Gold, silver, black embossing or debossing. Textured paper design.
Should not have
- A cheap look and feel.

```html
<!DOCTYPE html>
<html lang="en">
<head>
<meta charset="utf-8">
<title>528BUILDA Business Card</title>
<link href="https://fonts.googleapis.com/css2?family=Montserrat:wght@400;500;700&display=swap" rel="stylesheet">
<style>
  :root{
    --stage:#2b2b2b;
    --ink:#111111;
    --card-black:#0d0d0d;
    --tile-dark:#1c1c1c;
    --tile-light:#3a3a3a;
    --paper:#ffffff;
    --orange:#f7941d;
    --white:#ffffff;
  }
  *{margin:0;padding:0;box-sizing:border-box}
  html,body{width:1200px;height:1186px;overflow:hidden}
  body{background:var(--stage);font-family:"Montserrat",sans-serif;position:relative}

  .card{position:absolute;left:220px;width:760px;height:434px;border-radius:26px;overflow:hidden}
  .card-front{top:110px;background:var(--card-black)}
  .card-back{top:640px;background:var(--paper)}

  .front-pattern{position:absolute;inset:0;
    background:linear-gradient(160deg,var(--tile-light) 0%,var(--tile-dark) 45%,var(--card-black) 100%)}

  .wordmark{position:absolute;font-weight:500;letter-spacing:3px;white-space:nowrap;line-height:1}
  .card-front .wordmark{left:50%;top:50%;transform:translate(-50%,-50%);color:var(--white);font-size:58px}
  .card-back .wordmark{left:60px;top:196px;color:var(--ink);font-size:34px;letter-spacing:2px}

  .contact{position:absolute;left:398px;top:110px;padding-left:22px;border-left:2px solid var(--orange);height:160px}
  .contact-name{color:var(--orange);font-weight:700;font-size:30px;line-height:1.1}
  .contact-role{color:var(--ink);font-size:17px;margin-bottom:14px}
  .contact-line{display:flex;align-items:center;gap:10px;color:var(--ink);font-size:17px;line-height:1.55}
  .contact-line svg{width:14px;height:14px;flex:none}

  .back-band{position:absolute;left:0;bottom:0;width:760px;height:180px}
  .address{position:absolute;right:40px;bottom:34px;color:var(--white);font-size:17px;letter-spacing:.3px}
</style>
</head>
<body>
  <section class="card card-front">
    <div class="front-pattern" role="img" aria-label="Decorative pattern of dark glossy square tiles"></div>
    <p class="wordmark">528BUILDA</p>
  </section>

  <section class="card card-back">
    <p class="wordmark">528BUILDA</p>

    <div class="contact">
      <p class="contact-name">Daniel Harper</p>
      <p class="contact-role">Managing Director</p>
      <p class="contact-line">
        <svg viewBox="0 0 16 16"><path fill="var(--orange)" d="M3 1l3 1 1 4-2 1.5a9 9 0 0 0 4.5 4.5L11 10l4 1 1 3-2 2C7 16 0 9 0 3z"/></svg>
        555-014-2280</p>
      <p class="contact-line">
        <svg viewBox="0 0 16 16"><rect x="1" y="3" width="14" height="10" rx="1" fill="var(--orange)"/><path d="M1 4l7 5 7-5" stroke="var(--white)" stroke-width="1.4" fill="none"/></svg>
        hello@buildastudio.com</p>
      <p class="contact-line">
        <svg viewBox="0 0 16 16"><circle cx="8" cy="8" r="7" fill="none" stroke="var(--orange)" stroke-width="2"/><path d="M1 8h14M8 1c-3 4-3 10 0 14M8 1c3 4 3 10 0 14" stroke="var(--orange)" stroke-width="1.4" fill="none"/></svg>
        www.buildastudio.com</p>
    </div>

    <svg class="back-band" viewBox="0 0 760 180" preserveAspectRatio="none">
      <path d="M0 180 L0 170 Q260 60 760 30 L760 180 Z" fill="var(--orange)"/>
      <path d="M0 180 L0 182 Q260 74 760 42 L760 180 Z" fill="var(--card-black)"/>
    </svg>
    <p class="address">418 Maple Grove Ave, #112 Fairview, OH 43010</p>
  </section>
</body>
</html>
```